Webdesign für Steuerberaterin
Zielgruppe
Ich bin Steuerberaterin. Meine Zielgruppe sind sowohl Privatpersonen als auch Unternehmer sowie Männer und Frauen.
Aufgabenstellung
Bitte mein Logo und Foto mit berücksichtigen. Ich möchte keine Website, auf der alle 'Reiter' als eine Seite von oben nach unten durchlaufen. Sondern wirklich einzelne, voneinander getrennte Seiten.

```html
<!DOCTYPE html>
<html lang="de">
<head>
<meta charset="utf-8">
<title>Maren Brodtke – Leistungen</title>
<link rel="stylesheet" href="https://fonts.googleapis.com/css2?family=EB+Garamond:wght@400;500&family=Noto+Sans:wght@400;700&family=PT+Sans&display=swap">
<style>
  :root{
    --navy:#1f252c;
    --gold:#b08a2e;
    --gold-line:#c9a23a;
    --band:#dcb63d;
    --text:#4a4a4a;
    --white:#ffffff;
    --grey-tri:#8a8a8a;
  }
  *{margin:0;padding:0;box-sizing:border-box}
  html,body{width:1200px;height:864px;overflow:hidden;background:var(--white)}
  .page{position:relative;width:1200px;height:864px;font-family:"Noto Sans",Verdana,sans-serif;color:var(--text)}
  .sidebar{position:absolute;left:0;top:0;width:307px;height:836px;background:var(--navy)}
  .nav{list-style:none;font-family:"PT Sans",sans-serif;font-size:14px}
  .nav li{position:absolute;left:79px}
  .nav a{text-decoration:none;color:var(--gold)}
  .nav .current a{color:var(--white)}
  .section-emblem{position:absolute;left:37px;top:400px;width:140px;height:288px;border-radius:70px;
    background:linear-gradient(180deg,#9a9386 0%,#eeece6 50%,#8f897c 100%)}
  .footer{position:absolute;left:0;bottom:0;width:1200px;height:28px;background:linear-gradient(180deg,#e2bd44,var(--band));
    font-family:"PT Sans",sans-serif;font-size:13px;color:var(--navy);line-height:28px;padding-left:80px}
  .footer a{color:var(--navy);text-decoration:none}
  .footer .sep{margin:0 8px}
  .brand{position:absolute;left:381px;top:110px;display:flex;align-items:center;gap:8px;
    font-family:"EB Garamond",serif;font-size:24px;font-weight:500;color:var(--gold)}
  .brand .dot{width:12px;height:12px;border-radius:50%;background:var(--gold)}
  .photo{position:absolute;left:381px;top:184px;width:259px;height:182px;
    background:linear-gradient(135deg,#e4ece6 0%,#c9ddd2 55%,#9fb6c9 100%)}
  .title{position:absolute;left:691px;top:130px;width:474px;text-align:center;
    font-family:"EB Garamond",serif;font-weight:400;font-size:25px;color:var(--gold)}
  .rule{position:absolute;left:691px;top:186px;width:474px;height:2px;background:var(--gold-line)}
  .services{position:absolute;left:693px;top:232px;width:470px;font-size:13px;line-height:19.5px}
  .services h2{font-size:13.5px;font-weight:700;line-height:19.5px}
  .services p{margin:0}
  .gap{margin-top:21px}
  .list{list-style:none}
  .list li{padding-left:17px;position:relative}
  .list li::before{content:"-";position:absolute;left:0}
  .more{position:absolute;left:1164px;top:807px}
</style>
</head>
<body>
<div class="page">
  <aside class="sidebar">
    <ul class="nav">
      <li style="top:183px"><a href="#">Über mich</a></li>
      <li class="current" style="top:249px"><a href="#">Leistungen</a></li>
      <li style="top:315px"><a href="#">Kontakt</a></li>
    </ul>
    <div class="section-emblem" role="img" aria-label="Großes metallisch schimmerndes Paragrafenzeichen"></div>
  </aside>

  <div class="brand"><span class="dot"></span>Maren Brodtke</div>
  <div class="photo" role="img" aria-label="Foto: Steuerformular mit Kugelschreiber"></div>

  <h1 class="title">Leistungen</h1>
  <div class="rule"></div>

  <section class="services">
    <h2>Einkommensteuererklärung</h2>
    <h2 class="gap" style="margin-top:22px">Betriebliche Steuererklärungen</h2>
    <p>z.B. Umsatzsteuererklärung, Gewerbesteuererklärung, etc.</p>
    <h2 class="gap">Finanzbuchführung</h2>
    <p>Ich erledige Ihre Buchführung nach den Grundsätzen<br>
    ordnungsgemäßer Buchführung. Dies sowohl digital,<br>
    als auch auf Basis von Papierbelegen,<br>
    die Sie bei mir einreichen („Pendelordner“), je nachdem,<br>
    wie Sie es sich wünschen.<br>
    Sie möchten in die Digitalisierung einsteigen,<br>
    haben es aber bisher nicht geschafft? Dann lassen Sie uns<br>
    diesen Weg gemeinsam gehen!<br>
    Falls Sie selbst buchen (wollen), unterstütze ich Sie hierbei<br>
    natürlich auch gerne.</p>
    <p class="gap">Meine Buchführungs-Leistungen beinhalten u.a.:</p>
    <ul class="list">
      <li>Kontierung und Erfassung der Geschäftsvorfälle</li>
      <li>Ggf. Erfassung Ihrer gesamten Eingangs- und Ausgangsrechnungen sowie Übersicht der offenen Posten</li>
      <li>Laufende Abstimmung der Konten</li>
      <li>Regelmäßige Auswertungen (BWA, SuSa, etc.)</li>
      <li>...</li>
    </ul>
    <h2 style="margin-top:50px">Jahresabschluss (Bilanz)</h2>
  </section>

  <svg class="more" width="24" height="12" viewBox="0 0 24 12" aria-hidden="true">
    <polygon points="0,0 24,0 12,12" fill="var(--grey-tri)"/>
  </svg>

  <footer class="footer"><a href="#">Impressum</a><span class="sep">|</span><a href="#">Datenschutz</a></footer>
</div>
</body>
</html>
```